Website for new dental office

I am Dr. Colin Ashford and am building a new dental practice. I specialize in general dentistry. I am young and have a higher end dental practice incorporating very new technologies and would like my website to reflect that. As many dental patients are older, the website must be very easy to navigate. I would like patients to be able to request appointments, and will eventually add on patient information forms (the health history, etc, that you normally fill out in the practice) from my practice management software, so leave an area for that.

Industry/Entity Type

Building

```html
<!DOCTYPE html>
<html lang="en">
<head>
<meta charset="utf-8">
<title>Ashford Dental Clinic</title>
<link href="https://fonts.googleapis.com/css2?family=Oswald:wght@400;500&family=Open+Sans:wght@300;400;600;700&display=swap" rel="stylesheet">
<style>
:root{
  --brand:#0a8cf0;
  --ink:#1f1f1f;
  --text:#555;
  --footer-bg:#f4f4f4;
  --white:#fff;
  --line:#d8d8d8;
}
*{box-sizing:border-box;margin:0;padding:0}
html,body{width:1140px;height:1200px;overflow:hidden;background:var(--white)}
body{position:relative;font-family:"Open Sans",sans-serif;color:var(--text)}
.site-header{position:absolute;left:0;top:0;width:1140px;height:75px;background:var(--brand)}
.logo{position:absolute;left:170px;top:20px;font-family:"Oswald",sans-serif;font-weight:500;font-size:25px;color:var(--white);letter-spacing:-.3px}
.main-nav{position:absolute;right:166px;top:24px;display:flex;gap:21px}
.main-nav a{font-family:"Oswald",sans-serif;font-weight:500;font-size:17px;color:var(--white);text-decoration:none;text-transform:uppercase}
.hero{position:absolute;left:0;top:75px;width:1140px;height:393px;background:linear-gradient(100deg,#eef1f3 0%,#dfe5e8 35%,#7fcde6 65%,#41b8dd 100%)}
.hero-dots{position:absolute;left:466px;top:436px;display:flex;gap:6px}
.hero-dots span{width:15px;height:15px;border-radius:50%;background:#111}
.hero-dots span.active{background:var(--brand)}
.col{position:absolute;top:508px;width:272px}
.col h2{font-family:"Oswald",sans-serif;font-weight:500;font-size:23px;color:var(--brand);text-transform:uppercase;margin-bottom:14px}
.col p{font-size:12px;font-weight:300;line-height:26.4px;color:var(--text)}
.col p b{font-weight:700;color:var(--ink)}
.about{left:158px}
.services{left:439px}
.testimonials{left:719px}
.service-list{list-style:none;margin-top:12px}
.service-list li{display:flex;align-items:center;gap:10px;font-size:12px;font-weight:300;line-height:26.4px;padding-left:6px;white-space:nowrap}
.quote-mark{display:block;margin:3px 0 4px}
.testimonials p{line-height:21px}
.author{margin-top:11px;font-weight:600;font-size:14.5px;color:var(--ink)}
.author-company{font-size:12px;color:var(--ink)}
.cta{position:absolute;left:158px;top:828px;width:824px;height:85px;background:var(--brand)}
.cta p{position:absolute;left:44px;top:34px;width:520px;white-space:nowrap;font-size:13px;font-weight:700;color:var(--white)}
.cta-button{position:absolute;left:586px;top:23px;width:217px;height:41px;background:#222;color:var(--white);font-weight:600;font-size:15px;display:flex;align-items:center;justify-content:center;text-transform:uppercase}
.site-footer{position:absolute;left:0;top:941px;width:1140px;height:259px;background:var(--footer-bg)}
.f-col{position:absolute;top:25px}
.f-col h3{font-weight:300;font-size:16.5px;color:#444;margin-bottom:18px}
.f-col ul{list-style:none}
.f-col li{font-size:12.5px;font-weight:300;color:#333;line-height:21px}
.quick{left:158px}.support{left:369px}
.newsletter{left:581px;width:196px}
.newsletter p{font-size:12.5px;font-weight:300;line-height:21px;color:#333;margin-top:-4px}
.field{display:block;width:194px;height:24px;border:1px solid var(--line);background:var(--white);font-size:9.5px;color:#999;padding:5px 6px;margin-top:13px}
.subscribe{position:absolute;left:109px;top:167px;width:86px;height:21px;border-radius:11px;background:var(--brand);color:var(--white);font-size:13px;text-align:center;line-height:21px}
.connect{left:861px;width:127px}
.social li{display:flex;align-items:center;justify-content:space-between;height:33px;font-size:12.5px;font-weight:300;color:#333}
.social .dot{width:24px;height:24px;border-radius:50%;background:var(--brand)}
.copyright{position:absolute;left:0;width:1140px;top:226px;text-align:center;font-size:12px;font-weight:300;color:#444;padding-right:10px}
</style>
</head>
<body>
<header class="site-header">
  <div class="logo">ASHFORD DENTAL CLINIC</div>
  <nav class="main-nav"><a>Home</a><a>About Us</a><a>Services</a><a>FAQ's</a><a>Contact Us</a></nav>
</header>

<section class="hero" role="img" aria-label="Photo of a modern dental treatment room with a reclined patient chair"></section>
<div class="hero-dots"><span class="active"></span><span></span><span></span></div>

<section class="col about">
  <h2>About Us</h2>
  <p>Lorem Ipsum is simply dummy text of the printing and typesetting industry. Lorem Ipsum has been the industry's standard dummy text ever since the 1500s, when an unknown printer took a galley of type and scrambled it to make a type specimen book. It has survived not only five centuries, but also the leap into electronic typesetting, remaining essentially ...<b>Read More</b></p>
</section>

<section class="col services">
  <h2>Services</h2>
  <p>Lorem Ipsum is simply dummy text of the printing and typesetting industry. Lorem Ipsum has been the industry's standard dummy text</p>
  <ul class="service-list">
    <li><svg width="14" height="14" viewBox="0 0 14 14"><circle cx="7" cy="7" r="7" fill="#111"/><path d="M5.5 4l3 3-3 3" stroke="#fff" stroke-width="1.8" fill="none"/></svg>Ever since the 1500s, when an unknown</li>
    <li><svg width="14" height="14" viewBox="0 0 14 14"><circle cx="7" cy="7" r="7" fill="#111"/><path d="M5.5 4l3 3-3 3" stroke="#fff" stroke-width="1.8" fill="none"/></svg>Printer took a galley of type and scrambled</li>
    <li><svg width="14" height="14" viewBox="0 0 14 14"><circle cx="7" cy="7" r="7" fill="#111"/><path d="M5.5 4l3 3-3 3" stroke="#fff" stroke-width="1.8" fill="none"/></svg>It to make a type specimen book</li>
    <li><svg width="14" height="14" viewBox="0 0 14 14"><circle cx="7" cy="7" r="7" fill="#111"/><path d="M5.5 4l3 3-3 3" stroke="#fff" stroke-width="1.8" fill="none"/></svg>It has survived not only five centuries</li>
  </ul>
</section>

<section class="col testimonials">
  <h2>Testimonials</h2>
  <svg class="quote-mark" width="26" height="20" viewBox="0 0 26 20"><path d="M11 2C5 4 1 8 1 13a5 5 0 1 0 6-5c.6-2 2.4-3.6 4.6-4.4zM25 2c-6 2-10 6-10 11a5 5 0 1 0 6-5c.6-2 2.4-3.6 4.6-4.4z" fill="#333"/></svg>
  <p>Lorem Ipsum is simply dummy text of the printing and typesetting industry. Lorem Ipsum has been the industry's standard dummy text ever since the 1500s, when an unknown printer took a galley of type and scrambled it to make a type specimen book.</p>
  <div class="author">Daniel Foster</div>
  <div class="author-company">Company name</div>
</section>

<section class="cta">
  <p>Neque porro quisquam est qui dolorem ipsum quia dolor sit amet, consectetur</p>
  <div class="cta-button">Make an Appointment</div>
</section>

<footer class="site-footer">
  <div class="f-col quick"><h3>Quick Links</h3>
    <ul><li>Home</li><li>About Us</li><li>Services</li><li>FAQs</li><li>Contact Us</li></ul></div>
  <div class="f-col support"><h3>Support Links</h3>
    <ul><li>Legal Notice</li><li>Privacy Policy</li><li>Terms &amp; Conditions</li><li>Help</li></ul></div>
  <div class="f-col newsletter"><h3>Newsletter SignUp</h3>
    <p>Sign-up for our daily emails by entering your information below:</p>
    <span class="field">Name</span>
    <span class="field">Enter Your E-Mail ID</span>
    <span class="subscribe">Subscribe</span></div>
  <div class="f-col connect"><h3>Connect With Us</h3>
    <ul class="social"><li><span class="dot"></span>Chirper</li><li><span class="dot"></span>FaceSpace</li><li><span class="dot"></span>LinkNet</li></ul></div>
  <div class="copyright">Copyright ©2014 &nbsp;Company Name - All rights reserved</div>
</footer>
</body>
</html>
```